professional business card design for technology company

We are a small technology consulting firm, specialising in consulting based around Cloud and Managed services. Our colour scheme is yellow, blue and white, as you can see in the logos. Although we are based in melbourne australia, due to the nature of our work, our clients can be located anywhere. We are looking for a clean, professional, positive look - similar to our company logo

Target Market(s)

small business

Industry/Entity Type

Business

Contact Information for Business Card

eye catching, designed to incorporate some level of raised printing. Must contain website address, phone number, name and job title

Requirements
Must have
• Logo (attached) - use of the same colour scheme

```html
<!DOCTYPE html>
<html lang="en">
<head>
<meta charset="utf-8">
<title>Nuvora Business Card</title>
<link rel="stylesheet" href="https://fonts.googleapis.com/css2?family=Lato:wght@400;700;900&display=swap">
<style>
  :root {
    --stage: #2a2a2c;
    --card-dark: #1c1d20;
    --card-dark-2: #26272b;
    --card-light: #ffffff;
    --blue: #2e8fd0;
    --yellow: #f2c500;
    --ink: #1a1a1a;
    --logo-grey: #3d3d3f;
    --white: #ffffff;
  }
  * { box-sizing: border-box; margin: 0; padding: 0; }
  html, body {
    width: 1200px; height: 873px; overflow: hidden;
    background: var(--stage);
    font-family: "Lato", Arial, sans-serif;
  }
  .stage {
    position: relative; width: 1200px; height: 873px;
    display: flex; align-items: center; justify-content: center; gap: 40px;
  }
  .card {
    position: relative; width: 540px; height: 309px; overflow: hidden;
    border-radius: 3px; box-shadow: 0 10px 30px rgba(0,0,0,.45);
  }

  /* Front */
  .card--front {
    background: linear-gradient(135deg, var(--card-dark-2), var(--card-dark) 60%);
  }
  .card--front .facets {
    position: absolute; inset: 0;
    background: linear-gradient(160deg, rgba(255,255,255,.04), rgba(0,0,0,0) 50%, rgba(255,255,255,.03));
  }
  .brand {
    position: absolute; display: flex; align-items: center; gap: 14px;
    font-weight: 700; letter-spacing: -1px;
  }
  .brand__dot { border-radius: 50%; background: var(--yellow); flex: none; }
  .card--front .brand { left: 118px; top: 100px; font-size: 62px; color: var(--white); }
  .card--front .brand__dot { width: 40px; height: 40px; }
  .tagline {
    position: absolute; right: 34px; top: 196px;
    color: var(--yellow); font-size: 14px; font-weight: 700;
  }
  .website {
    position: absolute; left: 30px; bottom: 26px;
    color: var(--blue); font-size: 16px; font-weight: 700;
  }

  /* Back */
  .card--back { background: var(--card-light); }
  .card--back .brand { left: 34px; top: 100px; font-size: 44px; color: var(--logo-grey); gap: 12px; }
  .card--back .brand__dot { width: 30px; height: 30px; }
  .divider {
    position: absolute; left: 300px; top: 20px; width: 3px; height: 230px;
    background: linear-gradient(to bottom, rgba(46,143,208,0), var(--blue) 50%, rgba(46,143,208,0));
  }
  .address {
    position: absolute; left: 34px; bottom: 44px;
    color: var(--blue); font-size: 15px; font-weight: 700; line-height: 1.35;
  }
  .person { position: absolute; left: 326px; top: 36px; }
  .person__name { color: var(--blue); font-size: 18px; font-weight: 700; }
  .person__role { color: var(--ink); font-size: 12px; font-weight: 700; margin-top: 2px; }
  .contacts { position: absolute; left: 326px; top: 140px; list-style: none; }
  .contacts li {
    display: flex; align-items: center; gap: 8px;
    color: var(--ink); font-size: 13.5px; margin-bottom: 6px;
  }
  .contacts svg { width: 20px; height: 20px; flex: none; }
  .band { position: absolute; right: 0; bottom: 0; width: 300px; height: 70px; }
</style>
</head>
<body>
<main class="stage">
  <section class="card card--front" aria-label="Card front">
    <div class="facets" role="img" aria-label="Dark faceted background texture"></div>
    <div class="brand"><span class="brand__dot"></span>Nuvora</div>
    <p class="tagline">Your Slogan / Tagline Here</p>
    <p class="website">www.nuvora.com</p>
  </section>

  <section class="card card--back" aria-label="Card back">
    <div class="brand"><span class="brand__dot"></span>Nuvora</div>
    <div class="divider"></div>
    <p class="address">2280 N. Harbor Lane #210<br>Bayview Springs, Florida 33990</p>
    <div class="person">
      <p class="person__name">Daniel K. Marlow</p>
      <p class="person__role">Broker / Owner</p>
    </div>
    <ul class="contacts">
      <li>
        <svg viewBox="0 0 20 20" aria-hidden="true"><circle cx="10" cy="10" r="10" fill="var(--yellow)"/><path d="M6 7c0 4 3 7 7 7l1-2-2-1-1 1c-1-.5-2-1.5-2.5-2.5l1-1-1-2z" fill="var(--ink)"/></svg>
        555-204-1187
      </li>
      <li>
        <svg viewBox="0 0 20 20" aria-hidden="true"><circle cx="10" cy="10" r="10" fill="var(--yellow)"/><rect x="7" y="5" width="6" height="10" rx="1" fill="none" stroke="var(--ink)" stroke-width="1.2"/></svg>
        555-318-6640
      </li>
      <li>
        <svg viewBox="0 0 20 20" aria-hidden="true"><circle cx="10" cy="10" r="10" fill="var(--yellow)"/><rect x="5.5" y="6.5" width="9" height="7" fill="none" stroke="var(--ink)" stroke-width="1.2"/><path d="M5.5 6.5 10 10.5 14.5 6.5" fill="none" stroke="var(--ink)" stroke-width="1.2"/></svg>
        dmarlow@nuvoramail.com
      </li>
    </ul>
    <svg class="band" viewBox="0 0 300 70" preserveAspectRatio="none" aria-hidden="true">
      <path d="M0 70 C10 40 25 38 50 38 L300 14 L300 70 Z" fill="var(--blue)"/>
      <path d="M6 70 C16 48 30 46 54 46 L300 22 L300 70 Z" fill="var(--card-light)"/>
    </svg>
  </section>
</main>
</body>
</html>
```